Corporate Business Card

Very professional, Modern, Not to busy, include phone address email, website
(253) 617-4930, 18761 52nd Avenue S, Kent, WA 98047, martin@plumlinegroup.com, varkoworks.com

Target Market(s)

Manufacturing

Industry/Entity Type

Aero, machining, manufacturing, Off road racing

Contact Information for Business Card

Phone, address email, website

```html
<!DOCTYPE html>
<html lang="en">
<head>
<meta charset="utf-8">
<title>Varko Works – Business Card</title>
<link rel="stylesheet" href="https://fonts.googleapis.com/css2?family=Montserrat:wght@400;500;700;800&display=swap">
<style>
  :root {
    --navy: #1a3670;
    --navy-band: #1f3f7e;
    --red: #d9262f;
    --silver: #c9cbcf;
    --ink: #1b1b1f;
    --paper: #ffffff;
    --backdrop: #2b2c30;
  }
  * { margin: 0; padding: 0; box-sizing: border-box; }
  html, body { width: 1200px; height: 1015px; overflow: hidden; }
  body {
    background: var(--backdrop);
    font-family: "Montserrat", sans-serif;
    position: relative;
  }
  .card {
    position: absolute;
    left: 250px;
    width: 700px;
    height: 400px;
    overflow: hidden;
    box-shadow: 0 10px 30px rgba(0,0,0,.45);
  }
  .card--back { top: 90px; background: var(--navy); }
  .card--front { top: 525px; background: var(--paper); }

  .wordmark {
    position: absolute;
    font-weight: 800;
    letter-spacing: .04em;
    text-transform: uppercase;
    line-height: 1;
    white-space: nowrap;
  }
  .card--back .wordmark {
    left: 150px; top: 140px;
    font-size: 62px;
    color: var(--silver);
  }
  .card--back .rule {
    position: absolute;
    left: 150px; top: 226px;
    width: 230px; height: 2px;
    background: var(--silver);
  }
  .card--front .wordmark {
    right: 60px; top: 60px;
    font-size: 40px;
    color: var(--navy);
  }
  .card--front .rule {
    position: absolute;
    right: 250px; top: 118px;
    width: 150px; height: 2px;
    background: var(--navy);
  }

  .address {
    position: absolute;
    left: 60px; top: 170px;
    font-size: 15px;
    font-weight: 500;
    color: var(--ink);
    line-height: 1.35;
    font-style: normal;
  }
  .contacts {
    position: absolute;
    left: 60px; top: 250px;
    list-style: none;
    font-size: 15px;
    font-weight: 500;
    color: var(--ink);
  }
  .contacts li {
    display: flex;
    align-items: center;
    gap: 10px;
    height: 22px;
  }
  .contacts svg { width: 14px; height: 14px; flex: none; }

  .stripes { position: absolute; left: 0; top: 0; width: 700px; height: 400px; }
</style>
</head>
<body>

<section class="card card--back" aria-label="Card back">
  <div class="wordmark">Varko Works</div>
  <div class="rule"></div>
</section>

<section class="card card--front" aria-label="Card front">
  <svg class="stripes" viewBox="0 0 700 400" aria-hidden="true">
    <polygon points="0,354 530,354 518,366 0,366" fill="var(--red)"/>
    <polygon points="0,374 540,374 575,305 700,305 700,400 0,400" fill="var(--navy-band)"/>
  </svg>

  <div class="wordmark">Varko Works</div>
  <div class="rule"></div>

  <address class="address">
    18761 52nd Avenue<br>
    S, Kent, WA 98047
  </address>

  <ul class="contacts">
    <li>
      <svg viewBox="0 0 16 16" aria-hidden="true"><path fill="var(--red)" d="M3 1h3l1.5 4-2 1.3a9 9 0 0 0 4.2 4.2L11 8.5l4 1.5v3a2 2 0 0 1-2 2A12 12 0 0 1 1 3a2 2 0 0 1 2-2z"/></svg>
      (253) 617-4930
    </li>
    <li>
      <svg viewBox="0 0 16 16" aria-hidden="true"><rect x="1" y="3" width="14" height="10" fill="var(--red)"/><path d="M1.5 3.5 8 9l6.5-5.5" stroke="#fff" stroke-width="1.3" fill="none"/></svg>
      martin@plumlinegroup.com
    </li>
    <li>
      <svg viewBox="0 0 16 16" aria-hidden="true"><circle cx="8" cy="8" r="7" fill="var(--red)"/><path d="M1 8h14M8 1c-3 3.5-3 10.5 0 14M8 1c3 3.5 3 10.5 0 14" stroke="#fff" stroke-width="1" fill="none"/></svg>
      www.varkoworks.com
    </li>
  </ul>
</section>

</body>
</html>
```